Commercial Rooftop Solar business needs a website

We need a website with fantastic appeal for a new company based in Melbourne called Tallow Ridge Energy. We design and install solar energy systems for commercial applications across Australia. Our market is to focus on small to medium businesses looking for solar solutions, but we will also provide our service for residential customers. We would like a beautiful 'front page' feel to our home page, using photographs of solar PV systems and/or natural imagery. Our logo uses the colours orange and black, which could easily be echoed in photographic imagery of sunset and sunrise, for example. The design should communicate quiet confidence and professionalism to a corporate marketplace.

NEW POINTS FOR BRIEF: This design also needs to be flexible to allow for additional future content, including a Support page with sub pages, FAQ's, and a Blog.

As part of this design project, we will require the coding for the website to be completed by the designer.

We have seen some websites, which we like the look and feel of: these are listed below.

brightvanepower.com.au:

• Beautiful images underlaying brief text selling points.
• Simple ‘front cover’ style home page with elegant drop-down menu, stylish simple font style.
• Home page invites exploration through the menu links, rather than trying to provide all the information up front.
• Company logo and name in the top left hand corner, contact details accessible at top right hand, seems consistent in most sites.

kelpworks.com.au

rumbofield.com:
• Same element as the others is the front-page style home page with beautiful images underlying text.

We have a webpage that we started uploading content to. You can use some of the content there in your designs: www.tallowridgeenergy.com.au

Technical Specifications:
PAGES:

Home

About Us

Solutions - Commercial
- Residential

Products - Solar Panels - Vorla Heron, Vorla TELD, Vorla QB
- Solar Inverters - Kestamo, BrilQuill
- Monitoring systems - Dunmere Metrics
- Batteries - RW

- Datasheets have been provided for reference but if it's too much work, you can use generic text and we will provide content later.

Contact Us

FUTURE PAGES (Please consider in structure, where links could be placed):

Support

FAQ's

Blog.

We could provide some content for the Support page soon, but the Blog and FAQ's are future pages which we don't want highlighted in the design as we don't yet have content.

Phone: 1800 7 BIRCH
Email: sales@tallowridgeenergy.com.au

Currently, I do not have images and text available. Please
use placeholders in the meantime. The final text and images will be uploaded for the winner once a winning design has been selected.

Target Market(s)

Primary focus is on small to medium sized business owners. Those owners will have a house which may be suitable for solar so we want to cater to residential deeper in the website.

Industry/Entity Type

Solar Energy

Coding

Coded - Design and coding required

Number of Pages Required

5+ page

Colors
f78f20
0255a3

Requirements
Must have
• Logo as per attachments.
Nice to have
• Logo can have alternate colours Eg. White on Orange or Black etc. provided colour correct logo is shown somewhere eg. footer or contact page.
• In the active site, I'd like to have:
• Very slowly zooming images - barely perceptible.
• Title text that rolls into place
• Subtle movements
• See https://plumtally.com.au/ for example

```html
<!DOCTYPE html>
<html lang="en">
<head>
<meta charset="utf-8">
<title>About Us – Tallow Ridge Energy</title>
<link rel="stylesheet" href="https://fonts.googleapis.com/css2?family=Lato:wght@400;700&family=Michroma&display=swap">
<style>
:root{
  --orange:#ff3d14;
  --orange-soft:#f2a58c;
  --hero-top:#9a6a55;
  --hero-bottom:#3a3c4c;
  --photo-tone:#5d9ad6;
  --ink:#222;
  --text:#3a3a3a;
  --white:#fff;
  --footer:#1c1c1c;
  --footer-bar:#0e0e0e;
  --footer-rule:#555;
  --footer-text:#e8e8e8;
}
*{margin:0;padding:0;box-sizing:border-box}
html,body{width:1182px;height:1200px;overflow:hidden;background:var(--white)}
body{font-family:"Lato",sans-serif;color:var(--text);position:relative}
a{color:inherit;text-decoration:none}

/* Hero */
.hero{position:absolute;left:0;top:0;width:1182px;height:447px;overflow:hidden}
.hero-photo{position:absolute;inset:0;background:linear-gradient(180deg,var(--hero-top) 0%,var(--hero-bottom) 100%)}
.brand{position:absolute;left:160px;top:48px;display:flex;align-items:center;gap:10px;color:var(--white);font-size:22px;font-weight:700;letter-spacing:.5px}
.brand-dot{width:14px;height:14px;border-radius:50%;background:var(--white)}
.top-contact{position:absolute;left:727px;top:20px;display:flex;align-items:center;gap:16px}
.phone{display:flex;align-items:center;gap:8px;color:var(--white);font-size:17px;font-weight:700}
.phone svg{width:28px;height:28px}
.btn-estimate{display:flex;align-items:center;gap:10px;height:30px;padding:0 14px;border:2px solid var(--white);border-radius:16px;background:var(--orange);color:var(--white);font-size:12.5px;font-weight:700}
.main-nav{position:absolute;right:148px;top:82px;display:flex;gap:46px;font-family:"Michroma",sans-serif;font-size:10.5px;letter-spacing:2px;color:var(--white)}
.main-nav .active{color:var(--orange)}
.hero-title{position:absolute;left:141px;width:900px;top:232px;text-align:center;color:var(--white);font-size:28.5px;font-weight:700;line-height:35px;text-shadow:0 1px 3px rgba(0,0,0,.35)}

/* About */
.section-heading{position:absolute;left:0;top:494px;width:1182px;display:flex;justify-content:center;align-items:center;gap:8px;font-family:"Michroma",sans-serif;font-variant:small-caps;font-size:28px;letter-spacing:3px;color:var(--ink)}
.section-heading::before,.section-heading::after{content:"";width:75px;height:2px;background:var(--ink)}
.about-body{position:absolute;left:162px;top:580px;width:872px;font-size:12.2px;line-height:22.4px}
.about-photo{float:right;width:338px;height:205px;margin:5px 0 6px 27px;border-left:3px solid var(--orange-soft);border-bottom:3px solid var(--orange-soft);background:var(--photo-tone)}
.about-body p+p{margin-top:5px}

/* Footer */
.site-footer{position:absolute;left:0;top:933px;width:1182px;height:226px;background:var(--footer);color:var(--footer-text)}
.footer-col{position:absolute;top:30px}
.footer-col h3{white-space:nowrap;font-family:"Michroma",sans-serif;font-variant:small-caps;font-weight:400;font-size:13px;letter-spacing:2px;color:var(--white);padding-bottom:6px;border-bottom:1px dotted var(--footer-rule)}
.divider{position:absolute;top:50px;width:1px;height:130px;background:linear-gradient(180deg,transparent,#3a3a3a,transparent)}
.quick-links{left:157px;width:105px}
.quick-links ul{list-style:none;margin-top:6px}
.quick-links li{font-size:12px;height:31.5px;line-height:20px;padding-left:8px;position:relative}
.quick-links li::before{content:"›";position:absolute;left:-2px;color:#777}
.inquiry{left:354px;width:189px}
.inquiry form{margin-top:12px}
.field{display:block;width:189px;height:20px;background:var(--white);border:1px solid #ccc;border-radius:3px;font:10px "Lato",sans-serif;color:#444;padding:3px 6px;margin-bottom:5px}
.field.message{height:35px}
.btn-submit{margin-top:4px;width:68px;height:23px;border:none;border-radius:12px;background:var(--orange);color:var(--white);font-family:"Michroma",sans-serif;font-variant:small-caps;font-size:10px;letter-spacing:1px}
.contact{left:594px;width:198px}
.contact-row{display:flex;gap:8px;padding:9px 0;border-bottom:1px solid #2e2e2e;font-size:12px;line-height:15px}
.contact-row:last-child{border-bottom:none}
.contact-row svg{flex:none;width:12px;height:12px;margin-top:2px}
.contact-row strong{display:block;font-size:14px;font-weight:700;margin-bottom:3px}
.footer-brand{position:absolute;left:872px;top:100px;display:flex;align-items:center;gap:8px;color:var(--white);font-size:17px;font-weight:700}
.footer-brand span{width:12px;height:12px;border-radius:50%;background:var(--white)}
.copyright{position:absolute;left:0;top:1159px;width:1182px;height:41px;background:var(--footer-bar);color:var(--white);font-size:10.5px;text-align:center;line-height:41px}
</style>
</head>
<body>

<header class="hero">
  <div class="hero-photo" role="img" aria-label="Photo of a large solar panel field at sunset"></div>
  <a class="brand" href="#"><span class="brand-dot"></span>Tallow Ridge Energy</a>
  <div class="top-contact">
    <a class="phone" href="#">
      <svg viewBox="0 0 28 28"><circle cx="14" cy="14" r="12.5" fill="none" stroke="#fff" stroke-width="2"/><path d="M10 8c1-1 2 0 3 2s0 2-1 3c1 2 2 3 4 4 1-1 1-2 3-1s3 2 2 3c-1 2-3 2-5 1-3-2-5-4-7-7-1-2-1-4 1-5z" fill="#fff"/></svg>
      1800 7 BIRCH
    </a>
    <a class="btn-estimate" href="#">FREE ESTIMATE
      <svg width="20" height="20" viewBox="0 0 20 20" fill="none" stroke="#fff" stroke-width="1.4"><rect x="2" y="2" width="11" height="15" rx="1"/><path d="M5 7h5M5 10h5M5 13h3M12 17l6-7 1 1-6 7-2 0z"/></svg>
    </a>
  </div>
  <nav class="main-nav">
    <a href="#">HOME</a>
    <a class="active" href="#">ABOUT US</a>
    <a href="#">SOLUTIONS</a>
    <a href="#">CONTACT US</a>
  </nav>
  <h1 class="hero-title">Tallow Ridge Energy Is A National Company That<br>Specialises In Solar Solutions For The Commercial<br>And Residential</h1>
</header>

<main>
  <h2 class="section-heading">About Us</h2>
  <div class="about-body">
    <div class="about-photo" role="img" aria-label="Image of a solar panel and wind turbines in a green field"></div>
    <p>Tallow Ridge Energy is a national company that specialises in solar solutions for the commercial market. We also provide solutions for the residential market, bringing our uncompromising quality and service to the home.</p>
    <p>The founder of the company has over 10 years experience delivering projects on both a residential and commercial scale, having overseen the installation of more than 3 megawatts of solar projects. They were a pioneer on the first megawatt scale project in Australia.As a leader in the field, we offer cutting edge solar technology backed by industry leading warranties. All our systems are designed and installed by Clean Power Guild accredited persons. Our award winning designer will ensure your system will give the best long term performance and return on investment.</p>
    <p>Aenean id orci elementum, interdum diam in, viverra ipsum. Fusce molestie, turpis eget elementum imperdiet, sem mi ultricies quam, ut condimentum mi arcu vel ligula. Ut nec auctor libero, eu blandit augue. Curabitur et ipsum eros. Curabitur sit amet leo ut magna fringilla sagittis. Etiam tempus elit sapien, laoreet condimentum ligula suscipit at. Phasellus elementum id felis in molestie. Proin ac massa ullamcorper, euismod dolor et, suscipit ante. Pellentesque congue velit non vestibulum fermentum. Fusce pulvinar imperdiet eros, ac vulputate ipsum iaculis in. Sed at arcu orci. Cras fermentum felis eget magna dictum suscipit.</p>
  </div>
</main>

<footer class="site-footer">
  <div class="footer-col quick-links">
    <h3>Quick Links</h3>
    <ul><li>Home</li><li>About Us</li><li>Solutions</li><li>Contact Us</li></ul>
  </div>
  <span class="divider" style="left:310px"></span>
  <div class="footer-col inquiry">
    <h3>Quick Inquiry</h3>
    <form>
      <div class="field">Name</div>
      <div class="field">Email</div>
      <div class="field message">Message</div>
      <button class="btn-submit" type="button">Submit</button>
    </form>
  </div>
  <span class="divider" style="left:565px"></span>
  <div class="footer-col contact">
    <h3>Contact Details</h3>
    <div class="contact-row">
      <svg viewBox="0 0 12 12"><path d="M6 0a4 4 0 0 1 4 4c0 3-4 8-4 8S2 7 2 4a4 4 0 0 1 4-4z" fill="#ff3d14"/><circle cx="6" cy="4" r="1.5" fill="#1c1c1c"/></svg>
      <div><strong>TALLOW RIDGE ENERGY</strong>123 euismod cidun ut aoreetmok laoreet dol magnak aliquam</div>
    </div>
    <div class="contact-row">
      <svg viewBox="0 0 12 12"><path d="M2 1c1-1 2 0 3 2 0 1-1 1-1 2 1 2 2 3 3 3 1 0 1-1 2-1 2 1 3 2 2 3-1 2-4 1-6-1S1 3 2 1z" fill="#ff3d14"/></svg>
      <div>1800 7 BIRCH</div>
    </div>
    <div class="contact-row">
      <svg viewBox="0 0 12 12"><rect x="0" y="2" width="12" height="8" fill="#ff3d14"/><path d="M0 2l6 5 6-5" fill="none" stroke="#1c1c1c" stroke-width="1"/></svg>
      <div>info@tallowridgeenergy.com.au</div>
    </div>
  </div>
  <span class="divider" style="left:836px"></span>
  <div class="footer-brand"><span></span>Tallow Ridge Energy</div>
</footer>
<div class="copyright">Copyright © 2017 Tallow Ridge Energy. All Right Reserved.</div>

</body>
</html>
```